Harborview Optical -Window Poster (Optometrist)

We are an optometry practice and we need a poster for a new store promotion for our window highlighting we now also sell 2 pairs of glasses as a package deal. The size will be 1300mm width x 1900mm height

The artwork will be displayed as a fabric banner in our shop window. We have 7 other banners with different services our business provides. The words needs to standout for passers by and the cars stopped at the traffic lights out front of our business. We already have signs with our logos phone number etc. so we won't need them included in the poster.

It would need to include the following information.

Two pair packages now available*

*Conditions apply

The artwork will be displayed as a fabric banner in our shop window. We have 7 other banners with different services our business provides. The words needs to standout for passers by and the cars stopped at the traffic lights out front of our business. We already have signs with our logos phone number etc. so we won't need them included in the poster. Thank you for your work it's amazing Added Saturday, February 18, 2017

The artwork will be displayed as a fabric banner in our shop window. We have 7 other banners with different services our business provides. The words needs to standout for passers by and the cars stopped at the traffic lights out front of our business. We already have signs with our logos phone number etc. so we won't need them included in the poster. Added Saturday, February 18, 2017

Target Market(s)

Cars driving past and stopped at traffic lights outside our store.

Industry/Entity Type

Optician

Requirements
Must have
• Poster must say:
• Two pair packages now available*
• *Conditions apply

```html
<!DOCTYPE html>
<html lang="en">
<head>
<meta charset="utf-8">
<title>Harborview Optical – Two Pair Packages Window Poster</title>
<link rel="stylesheet" href="https://fonts.googleapis.com/css2?family=Archivo+Black&family=Oswald:wght@600&display=swap">
<style>
  :root {
    --backdrop: #ececec;
    --sky-top: #2a3150;
    --sky-low: #1d2440;
    --ground: #2b2b30;
    --band: #0e0b1f;
    --white: #ffffff;
    --yellow: #f4ea0a;
    --retina-core: #e8483c;
    --retina-edge: #d9584e;
  }
  * { margin: 0; padding: 0; box-sizing: border-box; }
  html, body {
    width: 962px; height: 1200px; overflow: hidden;
    background: var(--backdrop);
  }
  .poster {
    position: absolute; left: 45px; top: 0;
    width: 872px; height: 1200px; overflow: hidden;
  }
  .poster__backdrop {
    position: absolute; inset: 0;
    background: linear-gradient(180deg, var(--sky-top) 0%, var(--sky-low) 38%, #232636 55%, var(--ground) 75%, #242428 100%);
  }
  .poster__retina {
    position: absolute; left: 42px; top: 136px; width: 762px; height: 694px;
    border-radius: 50%;
    background: radial-gradient(ellipse at 45% 50%, #c8303a 0%, var(--retina-core) 25%, var(--retina-edge) 70%, #d66a60 100%);
  }
  .poster__eyewear {
    position: absolute; left: 180px; top: 830px; width: 522px; height: 168px;
    border-radius: 80px;
    background: radial-gradient(ellipse at center, rgba(70,40,55,0.55) 0%, rgba(50,30,45,0.25) 60%, rgba(0,0,0,0) 100%);
  }
  .headline-small {
    position: absolute; left: 0; right: 0; top: 58px;
    text-align: center; padding-left: 48px;
    font-family: "Oswald", "Arial Narrow", sans-serif; font-weight: 600;
    font-size: 58px; letter-spacing: 1.5px; color: var(--white);
  }
  .headline-small sup { font-size: 64px; vertical-align: 18px; line-height: 0; }
  .band {
    position: absolute; left: 22px; width: 833px; height: 192px;
    background: var(--band);
    display: flex; align-items: center; justify-content: center;
    font-family: "Archivo Black", "Arial Black", sans-serif;
    line-height: 1;
  }
  .band--top { top: 229px; }
  .band--bottom { top: 601px; }
  .band__text--primary { color: var(--white); font-size: 128px; letter-spacing: 1px; }
  .band__text--accent { color: var(--yellow); font-size: 100px; padding-left: 70px; letter-spacing: 2px; }
  .terms {
    position: absolute; left: 110px; top: 1020px; width: 680px; height: 79px;
    border: 3px solid var(--white);
    display: flex; align-items: center; justify-content: center;
    font-family: "Oswald", "Arial Narrow", sans-serif; font-weight: 600;
    font-size: 44px; letter-spacing: 2px; color: var(--white);
  }
</style>
</head>
<body>
  <main class="poster">
    <div class="poster__backdrop" role="img" aria-label="Photographic backdrop of a night sky over a dark wooden tabletop"></div>
    <div class="poster__retina" role="img" aria-label="Photograph of a retina showing red blood vessels"></div>
    <div class="poster__eyewear" role="img" aria-label="Photograph of a pair of round dark-framed glasses on the tabletop"></div>

    <p class="headline-small">NOW AVAILABLE<sup>*</sup></p>

    <div class="band band--top"><span class="band__text--primary">TWO PAIR</span></div>
    <div class="band band--bottom"><span class="band__text--accent">PACKAGES</span></div>

    <p class="terms">*CONDITIONS APPLY</p>
  </main>
</body>
</html>
```